Computer consultant business card

Bexil Software is a newly started computer consulting company. It's a small one-man company that provides mostly Vornix applications but also websites in collaboration with designers. I'm running this company on the side of full time university studies.

I want the final design to be clean and memorable. Be creative! :)

Some inspiration:
http://www.pixelmarta.com/design/48317
http://www.pixelmarta.com/design/2739164/business-card-design-by-frostlynk
http://www.pixelmarta.com/design/604281/business-card-design-by-koralind-vestrabanu

See attachment for my company logo.
Updates

I would like to thank everyone for submitting! I'll need a couple of days to review and ultimately select a design.

Target Market(s)

Non-technical entrepreneurs and small companies.

Industry/Entity Type

University

Requirements
Must have
• My company logo.
In any way, both colors from my logo.
First- and last name, e-mail and phone number.
Double-sided design.
Nice to have
• Something creative with the symbol in my logo

```html
<!DOCTYPE html>
<html lang="en">
<head>
<meta charset="utf-8">
<title>Bexil Software – Business Card</title>
<link rel="stylesheet" href="https://fonts.googleapis.com/css2?family=Jost:wght@400;500&display=swap">
<style>
  :root {
    --stage: #a8865f;
    --label: #1e1a16;
    --ink: #2f2d2e;
    --blue: #4472b9;
    --white: #ffffff;
    --muted: #4a4a4a;
    --black: #050505;
    --slate-top: #2e2f33;
    --slate-bottom: #4a5b82;
  }
  * { margin: 0; padding: 0; box-sizing: border-box; }
  html, body {
    width: 1200px; height: 788px; overflow: hidden;
    background: var(--stage);
    font-family: "Jost", "Century Gothic", sans-serif;
  }
  .sheet { position: relative; width: 1200px; height: 788px; }

  .side-label {
    position: absolute; width: 526px; text-align: center;
    font-size: 20px; color: var(--label);
  }

  .card {
    position: absolute; width: 526px; height: 300px;
    border-radius: 18px; overflow: hidden;
    box-shadow: 0 4px 10px rgba(0,0,0,.35);
  }
  .card--light { background: var(--white); }
  .card--black {
    background: radial-gradient(ellipse 45% 40% at 18% 8%, #3a3a3a 0%, transparent 100%),
                radial-gradient(ellipse 35% 45% at 80% 85%, #4a4546 0%, transparent 100%),
                var(--black);
  }
  .card--slate {
    background: radial-gradient(ellipse 80% 70% at 70% 100%, var(--slate-bottom) 0%, var(--slate-top) 85%);
  }

  .brand { position: absolute; display: flex; align-items: center; }
  .brand__dot { border-radius: 50%; background: var(--blue); flex: none; }
  .brand__name { font-weight: 500; line-height: 1; letter-spacing: 1px; }

  .front .brand { left: 54px; top: 26px; }
  .front .brand__dot { width: 74px; height: 74px; margin-right: 20px; }
  .front .brand__name { font-size: 64px; color: var(--ink); }

  .front__band { position: absolute; right: 0; top: 0; width: 34px; height: 300px; }

  .contact { position: absolute; left: 57px; top: 152px; color: var(--ink); }
  .contact__name { font-size: 18px; font-weight: 500; color: var(--blue); }
  .contact__role { font-size: 13px; color: var(--muted); margin-top: 1px; }
  .contact__line { font-size: 15px; margin-top: 6px; }
  .contact__line:first-of-type { margin-top: 37px; }
  .contact__key { font-weight: 500; font-style: italic; margin-right: 4px; }

  .back .brand { left: 0; right: 0; justify-content: center; top: 90px; }
  .back .brand__dot { width: 106px; height: 106px; margin-right: 26px; }
  .back .brand__name { font-size: 92px; }
  .card--light .brand__name { color: var(--ink); }
  .card--black .brand__name, .card--slate .brand__name { color: var(--white); }

  .web {
    position: absolute; left: 0; right: 0; bottom: 26px; text-align: center;
    font-size: 18px; letter-spacing: 3.4px;
  }
  .card--light .web { color: var(--ink); }
  .card--black .web, .card--slate .web { color: var(--white); }
</style>
</head>
<body>
<main class="sheet">
  <p class="side-label" style="left:56px; top:34px;">Front</p>
  <p class="side-label" style="left:622px; top:34px;">Back - 1</p>
  <p class="side-label" style="left:53px; top:405px;">Back - 2</p>
  <p class="side-label" style="left:622px; top:405px;">Back - 3</p>

  <section class="card card--light front" style="left:56px; top:75px;">
    <div class="brand">
      <span class="brand__dot"></span>
      <span class="brand__name">bexil</span>
    </div>
    <div class="contact">
      <p class="contact__name">First Name Last Name</p>
      <p class="contact__role">Designation</p>
      <p class="contact__line"><span class="contact__key">p</span>: +12 345 6789</p>
      <p class="contact__line"><span class="contact__key">e</span>: info@bexilapps.com</p>
    </div>
    <svg class="front__band" viewBox="0 0 34 300" aria-hidden="true">
      <rect x="0" y="0" width="34" height="300" fill="var(--ink)"/>
      <polygon points="0,0 34,0 34,96 0,118" fill="var(--blue)"/>
    </svg>
  </section>

  <section class="card card--light back" style="left:622px; top:75px;">
    <div class="brand">
      <span class="brand__dot"></span>
      <span class="brand__name">bexil</span>
    </div>
    <p class="web">www.bexilapps.com</p>
  </section>

  <section class="card card--black back" style="left:53px; top:446px;" role="img" aria-label="Black card with soft perforated metal texture in two corners">
    <div class="brand">
      <span class="brand__dot"></span>
      <span class="brand__name">bexil</span>
    </div>
    <p class="web">www.bexilapps.com</p>
  </section>

  <section class="card card--slate back" style="left:622px; top:446px;">
    <div class="brand">
      <span class="brand__dot"></span>
      <span class="brand__name">bexil</span>
    </div>
    <p class="web">www.bexilapps.com</p>
  </section>
</main>
</body>
</html>
```